Quorva - corporate Business Card

We need a good look and innovative business card for a new start up company based in Los Angeles called "Quorva". We are in a payment business, including payment card, app, and ewallet. We are expert in online payment and Card not present (CNP) transaction.
We need an innovative, modern business card.

Our logo font is Aero Matics

Target Market(s)

Startup - Bank - Online Payment - Card Manufacturing

Industry/Entity Type

Startup

Contact Information for Business Card

phone: 555 014 7396 - Address: 4172 Marlowe blvd, Harlow Bay, NV 89911

Requirements
Must have
• Message: innovative, professional, expert, high tech, trust, online payment expert, security
Nice to have
• no comment
Should not have
• no Comment

```html
<!DOCTYPE html>
<html lang="en">
<head>
<meta charset="utf-8">
<title>Quorva business card</title>
<link href="https://fonts.googleapis.com/css2?family=Nunito+Sans:wght@400;600;800&display=swap" rel="stylesheet">
<style>
  :root {
    --brand-red: #b8202f;
    --brand-red-soft: #c4404c;
    --paper: #ffffff;
    --backdrop: #1c1c1e;
  }
  * { box-sizing: border-box; margin: 0; padding: 0; }
  html, body { width: 1200px; height: 900px; overflow: hidden; }
  body {
    background: var(--backdrop);
    font-family: "Nunito Sans", Arial, sans-serif;
    position: relative;
  }
  .card {
    position: absolute;
    left: 290px;
    width: 620px;
    height: 354px;
    border-radius: 26px;
    overflow: hidden;
  }
  /* Front */
  .card-front { top: 62px; background: var(--brand-red); }
  .front-disc {
    position: absolute;
    left: 190px; top: 57px;
    width: 240px; height: 240px;
    border-radius: 50%;
    background: var(--brand-red-soft);
  }
  .front-name {
    position: absolute;
    left: 0; right: 0; top: 137px;
    text-align: center;
    color: var(--paper);
    font-weight: 800;
    font-size: 70px;
    line-height: 80px;
    letter-spacing: 1px;
  }
  /* Back */
  .card-back { top: 484px; background: var(--paper); }
  .brand-lockup {
    position: absolute;
    top: 50px; left: 0; right: 0;
    display: flex; justify-content: center; align-items: center; gap: 14px;
  }
  .brand-dot {
    width: 62px; height: 62px; border-radius: 50%;
    background: var(--brand-red);
  }
  .brand-name {
    color: var(--brand-red);
    font-weight: 800;
    font-size: 58px;
    line-height: 62px;
  }
  .address {
    position: absolute;
    top: 128px; left: 0; right: 0;
    text-align: center;
    color: var(--brand-red);
    font-weight: 600;
    font-size: 13px;
  }
  .rule {
    position: absolute; left: 0; right: 0;
    top: 176px; height: 6px;
    background: var(--brand-red);
  }
  .band {
    position: absolute; left: 0; right: 0;
    top: 192px; bottom: 0;
    background: var(--brand-red);
  }
  .holder {
    position: absolute; left: 40px; bottom: 36px;
    color: var(--paper);
  }
  .holder-name { font-weight: 800; font-size: 24px; line-height: 28px; }
  .holder-role { font-weight: 400; font-size: 15px; }
  .contact {
    position: absolute; right: 32px; top: 212px;
    list-style: none;
    color: var(--paper);
    font-size: 15px; font-weight: 600;
    text-align: right;
  }
  .contact li { display: flex; align-items: center; justify-content: flex-end; gap: 10px; line-height: 26px; }
  .contact svg { width: 14px; height: 14px; fill: none; stroke: var(--paper); stroke-width: 1.6; }
</style>
</head>
<body>
  <section class="card card-front" aria-label="Card front">
    <div class="front-disc"></div>
    <div class="front-name">quorva</div>
  </section>

  <section class="card card-back" aria-label="Card back">
    <div class="brand-lockup">
      <span class="brand-dot"></span>
      <span class="brand-name">quorva</span>
    </div>
    <p class="address">4172 Marlowe blvd, Harlow Bay, NV 89911</p>
    <div class="rule"></div>
    <div class="band"></div>
    <ul class="contact">
      <li>555 014 7396
        <svg viewBox="0 0 16 16"><path d="M4 1.5l2.5 3-1.5 1.5a8 8 0 0 0 5 5l1.5-1.5 3 2.5-1.5 2.5C7 14 2 9 1.5 3z"/></svg></li>
      <li>dana@quorva.com
        <svg viewBox="0 0 16 16"><rect x="1.5" y="3.5" width="13" height="9"/><path d="M1.5 3.5l6.5 5 6.5-5"/></svg></li>
      <li>www.quorva.com
        <svg viewBox="0 0 16 16"><circle cx="8" cy="8" r="6.5"/><path d="M1.5 8h13M8 1.5c-3 3.5-3 9.5 0 13M8 1.5c3 3.5 3 9.5 0 13"/></svg></li>
    </ul>
    <div class="holder">
      <div class="holder-name">Dana Whitlock</div>
      <div class="holder-role">President</div>
    </div>
  </section>
</body>
</html>
```